Very visible CoWorking Building Sign overlooking downtown LA and 110 freeway

Our building is drab but very visible and in the best location. We need a great sign for our monolith that overlooks downtown LA and the 100 freeway. We are a new CoWorking business and would like to have a few things we do on the sign: private offices, virtual offices, CoWorking Lounge. Everything we have seen is ho-hum. Can you get us noticed? We need people to know what we do and that we are here but in a creative, professional, unique sign.
Target Market(s)
People who have a business in DTLA, remote workers and those who work from home who need a professional address.
Requirements
Must have
- Our logo (which can be somewhat reimagined) which has our address 2417 on it. The three things we focus on: Private Offices, Virtual Offices, CoWorking Lounge. Incorporate some Navy. Readable from several hundred feet away.
Nice to have
- Mural feel? Something inspirational in this crazy COVID times? Graphics? Color block. I like the idea of decorative but it has to be readable as a building sign. The same with the use of colors. Our colors are grays and navy but with a pop of the chartreuse (we have 2 velvet chartreuse chairs in the space). Helpful to view our website: Harborview2417.com.
Should not have
- Not too graffiti. Keep it professional but unique and wow.

```html
<!DOCTYPE html>
<html lang="en">
<head>
<meta charset="utf-8">
<title>Harborview 2417 Building Sign</title>
<link rel="stylesheet" href="https://fonts.googleapis.com/css2?family=Libre+Baskerville:wght@700&family=Playfair+Display:wght@400;700&display=swap">
<style>
  :root {
    --backdrop: #c1c1c1;
    --navy: #0d2a4e;
    --blue: #0062ad;
    --chartreuse: #8dc63f;
    --white: #ffffff;
  }
  * { margin: 0; padding: 0; box-sizing: border-box; }
  html, body {
    width: 1200px; height: 1097px; overflow: hidden;
    background: var(--backdrop);
  }
  .sign {
    position: absolute; left: 290px; top: 30px;
    width: 621px; height: 1037px;
    background: var(--navy);
    overflow: hidden;
    color: var(--white);
  }
  .sign-waves { position: absolute; inset: 0; }
  .brand {
    position: absolute; left: 0; right: 0; top: 108px;
    text-align: center;
    font-family: "Playfair Display", serif; font-weight: 400;
    font-size: 56px; letter-spacing: 2px; line-height: 1;
    color: var(--white);
  }
  .brand-rule {
    position: absolute; left: 253px; top: 183px;
    width: 115px; height: 9px; background: var(--white);
  }
  .service-icon {
    position: absolute; left: 65px;
    width: 140px; height: 140px; border-radius: 50%;
    background: var(--chartreuse);
    border: 2px solid var(--white);
  }
  .service-name {
    position: absolute; left: 242px;
    font-family: "Libre Baskerville", serif; font-weight: 700;
    font-size: 38px; line-height: 44px; letter-spacing: 1px;
    color: var(--white);
  }
  .divider {
    position: absolute; left: 242px; width: 178px; height: 1.5px;
    background: var(--white);
  }
  .phone {
    position: absolute; left: 0; right: 0; top: 818px;
    text-align: center;
    font-family: "Playfair Display", serif; font-weight: 700;
    font-size: 92px; line-height: 1; letter-spacing: 1px;
    color: var(--white);
  }
  .web-ribbon { position: absolute; left: 26px; top: 930px; width: 570px; height: 68px; }
  .web-address {
    position: absolute; left: 26px; top: 930px; width: 570px; height: 68px;
    display: flex; align-items: center; justify-content: center;
    font-family: "Libre Baskerville", serif; font-weight: 700;
    font-size: 40px; color: var(--navy);
  }
</style>
</head>
<body>
  <div class="sign">
    <svg class="sign-waves" viewBox="0 0 621 1037" width="621" height="1037" aria-hidden="true">
      <path d="M0,700 C90,765 200,800 300,802 C200,790 90,760 0,722 Z" fill="var(--chartreuse)"/>
      <path d="M0,722 C120,795 260,812 380,790 C480,772 560,752 621,732 L621,1037 L0,1037 Z" fill="var(--blue)"/>
      <path d="M0,730 C120,803 260,820 380,798 C480,780 560,760 621,740" fill="none" stroke="var(--white)" stroke-width="7"/>
      <path d="M420,795 C500,782 570,768 621,755 L621,790 C560,788 490,790 420,795 Z" fill="var(--chartreuse)"/>
      <path d="M0,745 C110,812 250,830 370,812 C250,822 110,800 0,760 Z" fill="var(--blue)"/>
    </svg>

    <div class="brand">2417 HARBORVIEW</div>
    <div class="brand-rule"></div>

    <div class="service-icon" style="top:204px" role="img" aria-label="Icon of a private office desk with chair and lamp"></div>
    <div class="service-name" style="top:232px">PRIVATE<br>OFFICES</div>
    <div class="divider" style="top:371px"></div>

    <div class="service-icon" style="top:400px" role="img" aria-label="Icon of a reception desk with mail and a plant"></div>
    <div class="service-name" style="top:429px">VIRTUAL<br>OFFICES</div>
    <div class="divider" style="top:572px"></div>

    <div class="service-icon" style="top:598px" role="img" aria-label="Icon of people talking around a shared table"></div>
    <div class="service-name" style="top:624px">COWORKING<br>LOUNGE</div>

    <div class="phone">310.555.2417</div>

    <svg class="web-ribbon" viewBox="0 0 570 68" width="570" height="68" aria-hidden="true">
      <polygon points="0,0 570,0 540,34 570,68 0,68 30,34" fill="var(--white)"/>
    </svg>
    <div class="web-address">Harborview2417.com</div>
  </div>
</body>
</html>
```